​Silver Harbor Rhythm provides personal, friendly service in a fun and high energy environment. We are based in Vermont.

We would like a card that appeals to a wide range of audiences as we do a wide range of events. Please feel free to check out our website silverharborrhythm.net for inspiration.

Target Market(s)

weddings, corporate, birthday parties, colleges

Industry/Entity Type

Business

Contact Information for Business Card

Silver Harbor Rhythm
Providing Entertainment For All Occasions
555 274 9160
silverharborrhythm@mailnest.net
silverharborrhythm.net

```html
<!DOCTYPE html>
<html lang="en">
<head>
<meta charset="utf-8">
<title>Silver Harbor Rhythm – Business Card</title>
<link rel="stylesheet" href="https://fonts.googleapis.com/css2?family=Roboto:wght@300;400;700&display=swap">
<style>
  :root {
    --backdrop: #e9e6e1;
    --card-white: #ffffff;
    --brand-green: #1f6b45;
    --deep-green: #0d3f27;
    --mid-green: #15613c;
    --accent-red: #8c2a2c;
    --text-light: #ffffff;
    --card-shadow: 0 10px 28px rgba(0,0,0,0.22);
  }
  * { margin: 0; padding: 0; box-sizing: border-box; }
  html, body {
    width: 1200px; height: 913px; overflow: hidden;
    background: var(--backdrop);
    font-family: "Roboto", Arial, sans-serif;
  }
  .canvas { position: relative; width: 1200px; height: 913px; }
  .card {
    position: absolute; width: 520px; height: 300px;
    background: var(--card-white);
    box-shadow: var(--card-shadow);
    overflow: hidden;
  }
  .card--front { left: 70px; top: 130px; }
  .card--back { left: 610px; top: 480px; }

  .brand {
    display: flex; align-items: center; gap: 12px;
    font-weight: 700; color: var(--brand-green);
    letter-spacing: 1px; text-transform: uppercase; white-space: nowrap;
  }
  .brand__mark { width: 14px; height: 14px; background: var(--accent-red); flex: none; }
  .card--front .brand {
    position: absolute; left: 0; right: 0; top: 0; bottom: 0;
    justify-content: center; font-size: 28px;
  }
  .card--back .brand {
    position: absolute; right: 34px; top: 42px; font-size: 19px;
  }
  .card--back .brand__mark { width: 11px; height: 11px; }

  .back-art { position: absolute; inset: 0; }

  .contact {
    position: absolute; left: 24px; bottom: 28px;
    list-style: none; color: var(--text-light); font-size: 13px;
  }
  .contact li { display: flex; align-items: center; gap: 9px; margin-top: 7px; }
  .contact__phone { font-size: 15px; }
  .contact svg { width: 16px; height: 16px; flex: none; }

  .tagline-block {
    position: absolute; right: 24px; bottom: 54px; text-align: right;
    color: var(--text-light);
  }
  .tagline-block__name { font-weight: 700; font-size: 16px; letter-spacing: 0.5px; }
  .tagline-block__line { font-weight: 300; font-size: 13px; margin-top: 3px; }
</style>
</head>
<body>
<main class="canvas">

  <section class="card card--front" aria-label="Card front">
    <div class="brand"><span class="brand__mark"></span>Silver Harbor Rhythm</div>
  </section>

  <section class="card card--back" aria-label="Card back">
    <svg class="back-art" viewBox="0 0 520 300" preserveAspectRatio="none" aria-hidden="true">
      <defs>
        <linearGradient id="greenBand" x1="0" y1="0" x2="0" y2="1">
          <stop offset="0" stop-color="#1d7a4b"/>
          <stop offset="0.55" stop-color="#15613c"/>
          <stop offset="1" stop-color="#0d3f27"/>
        </linearGradient>
      </defs>
      <path d="M0,166 Q280,166 520,82 L520,300 L0,300 Z" fill="url(#greenBand)"/>
      <path d="M0,158 Q280,158 520,72" fill="none" stroke="#8c2a2c" stroke-width="4"/>
    </svg>

    <div class="brand"><span class="brand__mark"></span>Silver Harbor Rhythm</div>

    <ul class="contact">
      <li class="contact__phone">
        <svg viewBox="0 0 16 16" aria-hidden="true"><circle cx="8" cy="8" r="8" fill="#b8302f"/><path d="M5 4.5c.6-.5 1.2-.4 1.5.2l.6 1.2c.2.4 0 .8-.3 1l-.5.4c.4.9 1.1 1.6 2 2l.4-.5c.3-.3.7-.4 1-.2l1.2.6c.6.3.7.9.2 1.5-.6.7-1.5.8-2.4.4C6.8 10.2 5.6 9 4.8 7.1c-.4-.9-.3-1.9.2-2.6z" fill="#fff"/></svg>
        555 274 9160
      </li>
      <li>
        <svg viewBox="0 0 16 16" aria-hidden="true"><circle cx="8" cy="8" r="8" fill="#b8302f"/><g fill="none" stroke="#fff" stroke-width="0.9"><circle cx="8" cy="8" r="4.5"/><ellipse cx="8" cy="8" rx="2" ry="4.5"/><path d="M3.5 8h9"/></g></svg>
        silverharborrhythm.net
      </li>
      <li>
        <svg viewBox="0 0 16 16" aria-hidden="true"><circle cx="8" cy="8" r="8" fill="#b8302f"/><rect x="4" y="5" width="8" height="6" fill="none" stroke="#fff" stroke-width="0.9"/><path d="M4 5l4 3.4L12 5" fill="none" stroke="#fff" stroke-width="0.9"/></svg>
        silverharborrhythm@mailnest.net
      </li>
    </ul>

    <div class="tagline-block">
      <p class="tagline-block__name">Silver Harbor Rhythm</p>
      <p class="tagline-block__line">Providing Entertainment For All Occasions</p>
    </div>
  </section>

</main>
</body>
</html>
```